Executive Business Card for Healthcare Company [Need Today]

I need a business card design for a healthcare company. The only branding the company has thus far is a logo. The cards will be utilized by company executives. The design I envision will be vibrant and appealing but with a corporate feel. They shouldn't be too casual or playful. I would like to complete this project TODAY if possible.

Target Market(s)

Healthcare vendors, other executives in healthcare and pharmaceuticals

Industry/Entity Type

Pharmaceutical

Contact Information for Business Card

See attachment

Font styles to use
Serif
Sans Serif

Colors

Designer to choose colors to be used in the design.

```html
<!DOCTYPE html>
<html lang="en">
<head>
<meta charset="utf-8">
<title>Corvina Health – Executive Business Card</title>
<link rel="stylesheet" href="https://fonts.googleapis.com/css2?family=Open+Sans:wght@300;400;700&display=swap">
<style>
  :root {
    --page-bg: #e9ecec;
    --front-green: #47a977;
    --back-teal: #38bfc4;
    --paper: #ffffff;
    --ink: #1d2a30;
    --icon-green: #4cb07a;
    --brand-teal: #2cb8bf;
    --shadow: rgba(20, 40, 40, 0.22);
  }
  * { box-sizing: border-box; margin: 0; padding: 0; }
  html, body {
    width: 1200px; height: 1000px; overflow: hidden;
    background: var(--page-bg);
    font-family: "Open Sans", Arial, sans-serif;
  }
  .canvas { position: relative; width: 1200px; height: 1000px; }

  .card {
    position: absolute; width: 640px; height: 366px;
    border-radius: 22px; overflow: hidden;
    box-shadow: 0 14px 30px var(--shadow);
  }

  /* Front */
  .card-front { left: 70px; top: 70px; background: var(--front-green); }
  .front-brand {
    position: absolute; left: 0; right: 0; top: 0; bottom: 0;
    display: flex; align-items: center; justify-content: center; gap: 26px;
  }
  .brand-dot {
    width: 120px; height: 120px; border-radius: 50%;
    border: 3px solid var(--paper);
  }
  .brand-divider { width: 1px; height: 110px; background: rgba(255,255,255,0.7); }
  .front-brand .brand-name {
    color: var(--paper); font-weight: 300; font-size: 46px; letter-spacing: 0.5px;
  }

  /* Back */
  .card-back { left: 490px; top: 560px; background: var(--paper); }
  .back-panel {
    position: absolute; left: 0; top: 0; bottom: 0; width: 385px;
    background: var(--back-teal);
  }
  .holder { position: absolute; left: 40px; bottom: 92px; }
  .holder-name {
    color: var(--paper); font-weight: 700; font-size: 24px; letter-spacing: 0.5px;
  }
  .holder-title { color: var(--ink); font-size: 17px; margin-top: 2px; }

  .contact-list { position: absolute; left: 370px; top: 46px; list-style: none; }
  .contact-item { display: flex; align-items: flex-start; margin-bottom: 20px; }
  .contact-icon {
    flex: none; width: 30px; height: 30px; border-radius: 50%;
    background: var(--paper); display: flex; align-items: center; justify-content: center;
    margin-right: 14px; margin-top: 2px;
  }
  .contact-text { color: var(--ink); font-size: 14.5px; line-height: 1.35; }

  .back-brand {
    position: absolute; right: 28px; bottom: 34px;
    display: flex; align-items: center; gap: 12px;
  }
  .back-brand .brand-dot { width: 56px; height: 56px; border: 2px solid var(--icon-green); }
  .back-brand .brand-divider { height: 48px; background: #9dd; }
  .back-brand .brand-name { color: var(--brand-teal); font-weight: 300; font-size: 24px; }
</style>
</head>
<body>
<main class="canvas">

  <section class="card card-front" aria-label="Card front">
    <div class="front-brand">
      <span class="brand-dot"></span>
      <span class="brand-divider"></span>
      <span class="brand-name">Corvina Health</span>
    </div>
  </section>

  <section class="card card-back" aria-label="Card back">
    <div class="back-panel"></div>

    <div class="holder">
      <p class="holder-name">DANIEL HARLOW</p>
      <p class="holder-title">Senior Director of Marketing</p>
    </div>

    <ul class="contact-list">
      <li class="contact-item">
        <span class="contact-icon">
          <svg width="14" height="16" viewBox="0 0 14 16"><path d="M7 0C3.5 0 1 2.6 1 5.8 1 10 7 16 7 16s6-6 6-10.2C13 2.6 10.5 0 7 0z" fill="var(--icon-green)"/><circle cx="7" cy="6" r="2.2" fill="#fff"/></svg>
        </span>
        <p class="contact-text">Corvina Health, LLC<br>518 W Maple Avenue<br>Dayton, OH 45402</p>
      </li>
      <li class="contact-item">
        <span class="contact-icon">
          <svg width="16" height="16" viewBox="0 0 16 16"><path d="M3.6 1.2l2.3 2.7-1.3 1.8c.9 2 2.6 3.7 4.6 4.6l1.8-1.3 2.7 2.3-1.2 2.4C7 13.5 2.5 9 1.3 2.4z" fill="var(--icon-green)"/></svg>
        </span>
        <p class="contact-text">555-210-4478 (Office)<br>555-382-6015 (Cell)</p>
      </li>
      <li class="contact-item">
        <span class="contact-icon">
          <svg width="16" height="12" viewBox="0 0 16 12"><rect x="0.5" y="0.5" width="15" height="11" rx="1.5" fill="var(--icon-green)"/><path d="M1.5 1.5L8 7l6.5-5.5" fill="none" stroke="#fff" stroke-width="1.3"/></svg>
        </span>
        <p class="contact-text">dharlow@corvinarx.com</p>
      </li>
    </ul>

    <div class="back-brand">
      <span class="brand-dot"></span>
      <span class="brand-divider"></span>
      <span class="brand-name">Corvina Health</span>
    </div>
  </section>

</main>
</body>
</html>
```